Small Business Broker Business Card Design

A business card design for a small business brokerage, which is a financial service, not unlike real estate brokerage, but for small businesses such as laundromats, pizza shops, restaurants, cleaners etc. The designs should all be simple, more conservative in nature, using the colors and font of the logo. Again, think real estate Brokerage as a business context
Contact Information for Business Card
Name: Glen R. Harlow. Title: Small Business Advisor. Email: g.harlow@bayfieldcapitalworks.example. Mobile: (555) 274-3918. Office: (555) 806-2147. www.bayfieldcapitalworks.example

```html
<!DOCTYPE html>
<html lang="en">
<head>
<meta charset="utf-8">
<title>Bayfield Capital Works – Business Card</title>
<link rel="stylesheet" href="https://fonts.googleapis.com/css2?family=Montserrat:wght@400;500;600;700&display=swap">
<style>
  :root {
    --navy: #1f3a6e;
    --navy-deep: #1a3263;
    --green: #8cc63f;
    --paper: #ffffff;
    --backdrop: #b5b5b5;
    --ink: #1f3a6e;
  }
  * { box-sizing: border-box; margin: 0; padding: 0; }
  html, body { width: 1200px; height: 900px; overflow: hidden; }
  body {
    background: var(--backdrop);
    font-family: "Montserrat", Arial, sans-serif;
    position: relative;
  }
  .card {
    position: absolute;
    left: 320px;
    width: 560px;
    height: 320px;
    border-bottom: 4px solid var(--green);
    box-shadow: 0 6px 18px rgba(0,0,0,0.25);
    overflow: hidden;
  }
  .card--front { top: 80px; background: var(--paper); }
  .card--back { top: 490px; background: var(--navy-deep); }

  /* front */
  .brand-block {
    position: absolute;
    left: 70px; top: 48px;
    width: 140px; height: 140px;
    background: var(--navy);
  }
  .divider {
    position: absolute;
    left: 250px; top: 40px;
    width: 1.5px; height: 150px;
    background: var(--navy);
  }
  .person {
    position: absolute;
    left: 270px; top: 40px;
    color: var(--ink);
  }
  .person__name { font-size: 22px; font-weight: 700; letter-spacing: 0.2px; }
  .person__title { font-size: 11.5px; font-weight: 500; margin-top: 2px; }
  .contacts {
    position: absolute;
    left: 270px; top: 110px;
    list-style: none;
    color: var(--ink);
    font-size: 11px;
  }
  .contacts li { display: flex; align-items: center; gap: 8px; height: 19px; }
  .contacts svg { width: 11px; height: 11px; fill: var(--navy); flex: none; }

  .brand {
    position: absolute;
    display: flex; align-items: center; gap: 12px;
  }
  .brand__square { width: 22px; height: 22px; background: var(--navy); flex: none; }
  .brand__name {
    font-size: 22px; font-weight: 700; letter-spacing: 1.6px;
    text-transform: uppercase; color: var(--navy); white-space: nowrap;
  }
  .tagline {
    position: absolute;
    font-size: 10.5px; font-weight: 600; letter-spacing: 1.8px;
    text-transform: uppercase; color: var(--green); white-space: nowrap;
  }
  .card--front .brand { left: 70px; top: 226px; }
  .card--front .tagline { left: 71px; top: 260px; }

  /* back */
  .pattern-field {
    position: absolute; inset: 0;
    background: linear-gradient(160deg, #2b4a82 0%, #1f3a6e 45%, #1a3263 100%);
  }
  .card--back .brand { left: 96px; top: 168px; }
  .card--back .brand__square { background: var(--green); }
  .card--back .brand__name { color: var(--paper); font-size: 20px; }
  .card--back .tagline { left: 130px; top: 198px; font-size: 9.5px; }
</style>
</head>
<body>

<section class="card card--front" aria-label="Business card front">
  <div class="brand-block"></div>
  <div class="divider"></div>
  <div class="person">
    <p class="person__name">Glen R. Harlow</p>
    <p class="person__title">Small Business Advisor</p>
  </div>
  <ul class="contacts">
    <li>
      <svg viewBox="0 0 12 12" aria-hidden="true"><path d="M1 3c0-1 1-2 2-2h6c1 0 2 1 2 2v1H8V3H4v1H1zM2 5h8l1 6H1z"/></svg>
      (555) 806-2147
    </li>
    <li>
      <svg viewBox="0 0 12 12" aria-hidden="true"><rect x="3" y="0.5" width="6" height="11" rx="1.2"/><rect x="4" y="2" width="4" height="7" fill="#fff"/></svg>
      (555) 274-3918
    </li>
    <li>
      <svg viewBox="0 0 12 12" aria-hidden="true"><path d="M0.5 2.5h11v7h-11z"/><path d="M0.5 2.5l5.5 4 5.5-4" fill="none" stroke="#fff" stroke-width="1"/></svg>
      g.harlow@bayfieldcapitalworks.example
    </li>
    <li>
      <svg viewBox="0 0 12 12" aria-hidden="true"><circle cx="6" cy="6" r="5.5"/><path d="M0.5 6h11M6 0.5c-2.5 3-2.5 8 0 11M6 0.5c2.5 3 2.5 8 0 11" fill="none" stroke="#fff" stroke-width="0.8"/></svg>
      www.bayfieldcapitalworks.example
    </li>
  </ul>
  <div class="brand">
    <span class="brand__name">Bayfield Capital Works, Inc</span>
  </div>
  <p class="tagline">Confidently buy or sell a local business today</p>
</section>

<section class="card card--back" aria-label="Business card back">
  <div class="pattern-field" role="img" aria-label="Faint repeating pattern of the brand symbol on navy"></div>
  <div class="brand">
    <span class="brand__square"></span>
    <span class="brand__name">Bayfield Capital Works, Inc</span>
  </div>
  <p class="tagline">Confidently buy or sell a local business today</p>
</section>

</body>
</html>
```